Album Cover for Tunevale/Orchard Sound Neoclassical

I would like to get a new album cover design for a new release called 'Veldarine' by Tom Harwick. <br/>Some creative pointers - <br/>The meaning of veldarine is "the desire to care less about things..." to be a child again to be totally free. <br/>It is an album of upright piano solo pieces so perhaps some hint of an old retro upright piano as well as a sense of freedom. <br/>I like bright colour but equally I also like simple black & white.<br/>I am a fan of Lena Sorbeck and Pavel Ostrani so perhaps look at some of their covers as a guide. <br/>

Target Market(s)

20-40 yr old m&f - fans of Tobias Vennmark or Lena Sorbeck

Font styles to use
Serif

Colors

Designer to choose colors to be used in the design.

Requirements
Must have
• a sense of piano classical but more cinematic than formal/traditional classical
• Also a sense of freedom as above
Nice to have
• something modern looking as if it were a pop track but for classical
Should not have
• nothing too dark grey, dark green, dark sombre feel

```html
<!DOCTYPE html>
<html lang="en">
<head>
<meta charset="utf-8">
<title>Veldarine — Tom Harwick — Album Cover</title>
<link rel="stylesheet" href="https://fonts.googleapis.com/css2?family=Open+Sans:wght@800&family=Raleway:wght@200&display=swap">
<style>
  :root {
    --stage-bg: #dedede;
    --violet-light: #b800f6;
    --violet-deep: #8600c8;
    --piano-shadow: #2a0740;
    --piano-mid: #4a0a6e;
    --ink-white: #ffffff;
  }
  * { margin: 0; padding: 0; box-sizing: border-box; }
  html, body {
    width: 1200px;
    height: 1026px;
    overflow: hidden;
    background: var(--stage-bg);
  }
  .album-cover {
    position: absolute;
    left: 100px;
    top: 13px;
    width: 1000px;
    height: 1000px;
    overflow: hidden;
    background: linear-gradient(135deg, var(--violet-light) 0%, var(--violet-deep) 100%);
    box-shadow: 6px 8px 10px rgba(0, 0, 0, 0.25);
  }
  .cover-art {
    position: absolute;
    inset: 0;
    width: 1000px;
    height: 1000px;
  }
  .cover-frame {
    position: absolute;
    left: 17px;
    top: 12px;
    width: 966px;
    height: 962px;
    border: 6px solid var(--ink-white);
  }
  .artist-name {
    position: absolute;
    top: 42px;
    left: 0;
    width: 1000px;
    text-align: center;
    font-family: "Raleway", sans-serif;
    font-weight: 200;
    font-size: 70px;
    letter-spacing: 38px;
    padding-left: 38px;
    color: var(--ink-white);
    line-height: 1;
  }
  .album-title {
    position: absolute;
    left: 62px;
    top: 248px;
    font-family: "Open Sans", sans-serif;
    font-weight: 800;
    font-size: 226px;
    line-height: 233px;
    letter-spacing: -6px;
    color: var(--ink-white);
  }
  .album-title span { display: block; }
</style>
</head>
<body>
  <main class="album-cover">
    <svg class="cover-art" viewBox="0 0 1000 1000" role="img" aria-label="Photograph of a black grand piano on a patterned rug, tinted purple, seen from above at an angle">
      <defs>
        <linearGradient id="pianoTone" x1="0" y1="0" x2="1" y2="1">
          <stop offset="0" stop-color="var(--piano-mid)"/>
          <stop offset="1" stop-color="var(--piano-shadow)"/>
        </linearGradient>
      </defs>
      <polygon points="500,260 860,130 1000,150 1000,1000 900,1000 640,700 450,420 530,380"
               fill="url(#pianoTone)" opacity="0.9"/>
      <polygon points="500,700 650,640 1000,860 1000,1000 760,1000"
               fill="var(--piano-shadow)" opacity="0.45"/>
    </svg>
    <div class="cover-frame"></div>
    <p class="artist-name">TOM HARWICK</p>
    <h1 class="album-title">
      <span>VEL</span>
      <span>DAR</span>
      <span>INE</span>
    </h1>
  </main>
</body>
</html>
```